Business Card and Letterhead for Pimlu - modern real estate business

I need a double sided business card design for Pimlu. Please see business card brief here https://files.trelvonadocs.com/sheet/r/7QzTmWbaXLJnoPEd-kRyUgFhHsstbvCe2qfoMxDa_pz/view?mode=shared

Please feel free to design the business cards however you feel best. I am happy to give some creative freedoms and then provide feedback from there.

Please then also create a letterhead to match the business card design

Colors

Designer to choose colors to be used in the design.

Requirements
Must have
• Must be a modern, elegant business card which looks very professional

```html
<!DOCTYPE html>
<html lang="en">
<head>
<meta charset="utf-8">
<title>Pimlu Business Card</title>
<link rel="stylesheet" href="https://fonts.googleapis.com/css2?family=Montserrat:wght@400;500;600;700&display=swap">
<style>
  :root {
    --page-bg: #2a2a2a;
    --card-black: #050505;
    --brand-red: #e3202a;
    --text-white: #ffffff;
    --text-soft: #e8e8e8;
    --divider: rgba(255,255,255,0.55);
    --photo-dark: #1c1f18;
    --photo-mid: #3a4030;
    --photo-green: #4f5a36;
  }
  * { margin: 0; padding: 0; box-sizing: border-box; }
  html, body { width: 1200px; height: 900px; overflow: hidden; }
  body {
    background: var(--page-bg);
    font-family: "Montserrat", Arial, sans-serif;
    position: relative;
  }
  .card {
    position: absolute;
    left: 240px;
    width: 720px;
    height: 411px;
    overflow: hidden;
  }
  .card-front { top: 26px; background: var(--card-black); }
  .card-back { top: 463px; background: var(--photo-dark); }

  .brand-name {
    position: absolute;
    left: 0; right: 0; top: 130px;
    text-align: center;
    font-size: 104px;
    font-weight: 600;
    letter-spacing: 6px;
    color: var(--brand-red);
    line-height: 1;
  }
  .front-url {
    position: absolute;
    left: 0; right: 0; bottom: 44px;
    text-align: center;
    font-size: 15px;
    letter-spacing: 1.5px;
    color: var(--text-white);
  }
  .front-url strong { color: var(--brand-red); font-weight: 700; }

  .portrait-photo {
    position: absolute; inset: 0;
    background:
      radial-gradient(ellipse 30% 55% at 48% 70%, #15161a 0%, rgba(21,22,26,0) 100%),
      radial-gradient(ellipse 40% 50% at 85% 60%, var(--photo-green) 0%, rgba(79,90,54,0) 100%),
      radial-gradient(ellipse 35% 45% at 12% 35%, var(--photo-mid) 0%, rgba(58,64,48,0) 100%),
      linear-gradient(180deg, #34372f 0%, #2a2d24 50%, #23261d 100%);
  }
  .photo-shade { position: absolute; inset: 0; background: rgba(0,0,0,0.35); }

  .agent-block {
    position: absolute;
    right: 382px; top: 196px;
    text-align: right;
  }
  .agent-name {
    font-size: 30px;
    font-weight: 600;
    color: var(--brand-red);
    letter-spacing: 0.5px;
    line-height: 1.05;
  }
  .agent-title {
    font-size: 19px;
    font-weight: 400;
    color: var(--text-white);
    letter-spacing: 0.3px;
  }
  .contact-divider {
    position: absolute;
    left: 350px; top: 200px;
    width: 1px; height: 70px;
    background: var(--divider);
  }
  .contact-list {
    position: absolute;
    left: 366px; top: 198px;
    list-style: none;
  }
  .contact-list li {
    display: flex; align-items: center; gap: 10px;
    font-size: 20px;
    color: var(--text-white);
    letter-spacing: 0.8px;
    height: 26px;
  }
  .contact-list svg { width: 15px; height: 15px; flex: none; }
  .postal-address {
    position: absolute;
    left: 250px; top: 340px;
    font-size: 20px;
    color: var(--text-white);
    letter-spacing: 0.8px;
  }
  .accent-band-red {
    position: absolute; left: 0; bottom: 12px;
    width: 415px; height: 9px;
    background: var(--brand-red);
  }
  .accent-band-white {
    position: absolute; left: 422px; right: 0; bottom: 0;
    height: 9px;
    background: var(--text-white);
  }
</style>
</head>
<body>
  <section class="card card-front">
    <div class="brand-name">PIMLU</div>
    <p class="front-url">www.<strong>pimlu</strong>.com</p>
  </section>

  <section class="card card-back">
    <div class="portrait-photo" role="img" aria-label="Portrait photo of the agent in a dark suit, outdoors with trees and a valley behind"></div>
    <div class="photo-shade"></div>

    <div class="agent-block">
      <h1 class="agent-name">LIAM CARVER</h1>
      <p class="agent-title">Licenced Real Estate Agent</p>
    </div>

    <div class="contact-divider"></div>

    <ul class="contact-list">
      <li>
        <svg viewBox="0 0 16 16" aria-hidden="true"><path fill="#e3202a" d="M4 1.5l2.2 2.6-1.3 1.6c.8 1.8 2.2 3.3 4 4.2l1.6-1.3 2.7 2.1-1.2 2.6C6.6 13 2.7 9 2.3 3.3z"/></svg>
        0400 318 592
      </li>
      <li>
        <svg viewBox="0 0 16 16" aria-hidden="true"><rect x="1.5" y="3.5" width="13" height="9" fill="none" stroke="#e3202a" stroke-width="1.5"/><path d="M1.5 3.5l6.5 5 6.5-5" fill="none" stroke="#e3202a" stroke-width="1.5"/></svg>
        liam@pimlu.com
      </li>
      <li>
        <svg viewBox="0 0 16 16" aria-hidden="true"><g fill="none" stroke="#e3202a" stroke-width="1.3"><circle cx="8" cy="8" r="6.5"/><ellipse cx="8" cy="8" rx="3" ry="6.5"/><path d="M1.5 8h13M2.5 4.8h11M2.5 11.2h11"/></g></svg>
        www.pimlu.com
      </li>
    </ul>

    <p class="postal-address">PO Box 1739 Larkfield NSW 2790</p>

    <div class="accent-band-red"></div>
    <div class="accent-band-white"></div>
  </section>
</body>
</html>
```